Property management company looking for modern card design

We at Blue Heron Partners provides property management services for its residential and commercial properties, with expertise in all categories of multifamily, industrial and office projects throughout California.

We need a business card design that is professional and modern designed business card. In our field, clients get hundreds of business cards, we would like our card to stand out.

Please avoid small print.

Target Market(s)

Professionals and high end clients

Industry/Entity Type

Financial Planning

Contact Information for Business Card

Company Name: Blue Heron Partners, Name, email, license #, phone number, website blueheronpartners.com

Font styles to use
Sans Serif

Requirements
Must have
• The card design needs to be adaptable because there is a possibly we will be expanding into different sectors other than real estate. The card design should be focused on financial planning and asset management.
Nice to have
• Modern and simple business card. Eye catching. Non-standard size/shaped cards would be great.
• blueheronpartners.com
Should not have
• Too many bright color or any pictures or shapes of real estate stuff.

```html
<!DOCTYPE html>
<html lang="en">
<head>
<meta charset="utf-8">
<title>Blue Heron Partners – Business Card</title>
<link href="https://fonts.googleapis.com/css2?family=Montserrat:wght@300;400;600&display=swap" rel="stylesheet">
<style>
  :root {
    --backdrop: #e6e3df;
    --card-dark: #333333;
    --card-light: #ffffff;
    --accent: #cf3336;
    --ink: #2b2b2b;
    --rule-light: #8a8a8a;
    --rule-dark: #bdbdbd;
  }
  html, body {
    margin: 0;
    padding: 0;
    overflow: hidden;
  }
  .canvas {
    position: relative;
    width: 1200px;
    height: 1000px;
    background: var(--backdrop);
    font-family: "Montserrat", sans-serif;
    overflow: hidden;
  }
  .card {
    position: absolute;
    left: 288px;
    width: 625px;
    height: 358px;
    border-radius: 24px;
    box-sizing: border-box;
  }
  /* Front */
  .card-front {
    top: 140px;
    background: var(--card-dark);
  }
  .wordmark {
    position: absolute;
    left: 0;
    right: 0;
    top: 122px;
    text-align: center;
    color: var(--card-light);
  }
  .wordmark-name {
    margin: 0;
    font-weight: 300;
    font-size: 47px;
    letter-spacing: 1px;
    line-height: 1;
  }
  .wordmark-tagline {
    display: flex;
    align-items: center;
    justify-content: center;
    gap: 12px;
    margin-top: 18px;
    font-weight: 300;
    font-size: 23px;
    letter-spacing: 1px;
  }
  .wordmark-tagline::before,
  .wordmark-tagline::after {
    content: "";
    width: 126px;
    height: 1px;
    background: var(--rule-light);
  }
  /* Back */
  .card-back {
    top: 531px;
    background: var(--card-light);
  }
  .brand-disc {
    position: absolute;
    left: 86px;
    top: 90px;
    width: 180px;
    height: 180px;
  }
  .divider {
    position: absolute;
    left: 297px;
    top: 100px;
    width: 1px;
    height: 160px;
    background: linear-gradient(to bottom, transparent, var(--rule-dark) 20%, var(--rule-dark) 80%, transparent);
  }
  .contact {
    position: absolute;
    left: 326px;
    top: 98px;
    color: var(--ink);
  }
  .contact-name {
    margin: 0;
    font-weight: 600;
    font-size: 22px;
    color: var(--accent);
    line-height: 1.1;
  }
  .contact-role {
    margin: 2px 0 22px;
    font-size: 14px;
  }
  .contact-list {
    list-style: none;
    margin: 0;
    padding: 0;
    font-size: 14.5px;
    line-height: 25px;
  }
  .contact-label {
    color: var(--accent);
  }
</style>
</head>
<body>
<div class="canvas">
  <section class="card card-front">
    <div class="wordmark">
      <p class="wordmark-name">BLUE HERON</p>
      <div class="wordmark-tagline">PARTNERS</div>
    </div>
  </section>

  <section class="card card-back">
    <svg class="brand-disc" viewBox="0 0 180 180" aria-hidden="true">
      <circle cx="90" cy="90" r="90" fill="var(--accent)"/>
    </svg>
    <div class="divider"></div>
    <div class="contact">
      <p class="contact-name">Daniel Reyes</p>
      <p class="contact-role">President</p>
      <ul class="contact-list">
        <li>License: #7310486</li>
        <li><span class="contact-label">P</span>: 123-555-0142</li>
        <li><span class="contact-label">E</span>: info@blueheronpartners.com</li>
        <li>www.blueheronpartners.com</li>
      </ul>
    </div>
  </section>
</div>
</body>
</html>
```